Business Card Design needed for start up company Halvora

In need of a new business card designed for a start up company based in Sydney, Halvora is a new start up innovative Company, our mission it to make property accessible for everyday Australian and to become the leading Real Estate platform in Australia. We want it to be fresh and clean.

Industry/Entity Type

Financial

Contact Information for Business Card

Section for Name
Section for Title

HALVORA - The Strength of Pooling
Mobile:
Direct:

Font styles to use
Sans Serif

Colors
33a6d7
0692cd
0255a3
ffffff

Requirements
Must have
• Logo, all business card details

```html
<!DOCTYPE html>
<html lang="en">
<head>
<meta charset="UTF-8">
<title>Halvora Business Card</title>
<link href="https://fonts.googleapis.com/css2?family=Open+Sans:ital,wght@0,400;0,600;0,700;0,800;1,700&display=swap" rel="stylesheet">
<style>
  :root {
    --stage: #000000;
    --sky: #259bd6;
    --navy: #213f77;
    --ink: #1f4a8a;
    --white: #ffffff;
  }
  * { margin: 0; padding: 0; box-sizing: border-box; }
  html, body {
    width: 1200px;
    height: 900px;
    overflow: hidden;
    background: var(--stage);
    font-family: "Open Sans", sans-serif;
  }
  .canvas { position: relative; width: 1200px; height: 900px; }

  .card { position: absolute; top: 275px; width: 477px; height: 294px; }
  .card--front {
    left: 116px;
    background: var(--sky);
    border-radius: 0 62px 0 62px;
  }
  .card--back {
    left: 622px;
    background: var(--navy);
    border-radius: 62px 0 62px 0;
  }

  .identity {
    position: absolute;
    right: 19px;
    top: 34px;
    text-align: right;
    color: var(--white);
  }
  .identity__name { font-size: 19px; font-weight: 700; line-height: 1.1; }
  .identity__title { font-size: 13px; font-weight: 400; margin-top: 3px; }

  .brand { position: absolute; display: flex; align-items: center; }
  .brand__dot { border-radius: 50%; flex: none; }
  .brand__name {
    font-weight: 800;
    letter-spacing: -1px;
    line-height: 1;
  }
  .card--front .brand { left: 33px; top: 91px; }
  .card--front .brand__dot { width: 94px; height: 94px; background: var(--white); margin-right: 12px; }
  .card--front .brand__name { font-size: 56px; color: var(--ink); }

  .card--back .brand { left: 76px; top: 102px; }
  .card--back .brand__dot { width: 88px; height: 88px; background: var(--sky); margin-right: 12px; }
  .card--back .brand__name { font-size: 56px; color: var(--white); }

  .tagline {
    position: absolute;
    left: 0;
    right: 0;
    top: 232px;
    text-align: center;
    color: var(--white);
    font-size: 21px;
    font-weight: 700;
    font-style: italic;
    letter-spacing: -0.3px;
  }

  .contact {
    position: absolute;
    right: 19px;
    top: 206px;
    list-style: none;
    color: var(--white);
    font-size: 13px;
  }
  .contact__item {
    display: flex;
    justify-content: flex-end;
    align-items: center;
    height: 20px;
  }
  .contact__icon { width: 11px; height: 11px; margin-left: 10px; fill: var(--white); }
</style>
</head>
<body>
<main class="canvas">
  <section class="card card--front">
    <div class="identity">
      <p class="identity__name">Daniel Marsh</p>
      <p class="identity__title">Managing Director</p>
    </div>

    <div class="brand">
      <span class="brand__dot"></span>
      <span class="brand__name">HALVORA</span>
    </div>

    <ul class="contact">
      <li class="contact__item">(041)-555-0182
        <svg class="contact__icon" viewBox="0 0 12 12" aria-hidden="true"><path d="M2.4 0.6l2 2.1c.3.3.3.8 0 1.1l-.9.9c.7 1.5 1.9 2.7 3.4 3.4l.9-.9c.3-.3.8-.3 1.1 0l2.1 2c.3.3.3.8 0 1.1l-1 1c-.5.5-1.3.6-2 .3C4.8 10.4 1.6 7.2.4 4c-.3-.7-.2-1.5.3-2l1-1.4c.2-.2.5-.2.7 0z"/></svg>
      </li>
      <li class="contact__item">555-310-0427
        <svg class="contact__icon" viewBox="0 0 12 12" aria-hidden="true"><path d="M3.5 0h5c.6 0 1 .4 1 1v10c0 .6-.4 1-1 1h-5c-.6 0-1-.4-1-1V1c0-.6.4-1 1-1zm.3 1.3v8h4.4v-8zM6 9.8a.7.7 0 100 1.4.7.7 0 000-1.4z"/></svg>
      </li>
      <li class="contact__item">hello@halvora.com
        <svg class="contact__icon" viewBox="0 0 12 12" aria-hidden="true"><path d="M0 2.5h12v7H0zm1 .9v.3l5 3.2 5-3.2v-.3z"/></svg>
      </li>
    </ul>
  </section>

  <section class="card card--back">
    <div class="brand">
      <span class="brand__dot"></span>
      <span class="brand__name">HALVORA</span>
    </div>
    <p class="tagline">The Strength of Pooling</p>
  </section>
</main>
</body>
</html>
```